National Mission Critical Construction Contractor needs Stationery Design to make a bold statement

We are a small commercial construction company, working primarily in mission critical facilities across the U.S.. We have exciting corporate changes going an and a new logo and office space so we need new stationery. The final design should incorporate our new logo and invoke a fresh, high-tech feel while looking simple and modern.

Industry/Entity Type

Construction

Contact Information for Business Card

We are required to list our state licensing qualifications on the back of our card.

Font styles to use
Sans Serif

Requirements
Must have
• We need to have a design for second page of stationery, envelopes both standard and with a window and for a 3 x 4 notepad.

```html
<!DOCTYPE html>
<html lang="en">
<head>
<meta charset="utf-8">
<title>Harlow Ridge Construction – Business Card</title>
<link rel="stylesheet" href="https://fonts.googleapis.com/css2?family=Roboto:wght@400;500&display=swap">
<style>
  :root {
    --page-bg: #e6e8eb;
    --card-bg: #f6f8fa;
    --card-edge: #c9ced4;
    --brand-blue: #1f4f8f;
    --name-blue: #1d4c8c;
    --title-green: #58a12d;
    --body-text: #3a3f45;
    --icon-blue: #1f3f6e;
    --graphic-green: #5b9a2f;
    --graphic-teal: #2c77a6;
    --graphic-blue: #1c479a;
  }
  html, body {
    margin: 0;
    width: 1200px;
    height: 969px;
    overflow: hidden;
    background: var(--page-bg);
    font-family: "Roboto", Arial, sans-serif;
  }
  .business-card {
    position: absolute;
    left: 100px;
    top: 200px;
    width: 1000px;
    height: 570px;
    background: var(--card-bg);
    border: 1px solid var(--card-edge);
    box-sizing: border-box;
    overflow: hidden;
  }
  .brand-graphic {
    position: absolute;
    left: 545px;
    top: 0;
    width: 455px;
    height: 568px;
    background: linear-gradient(90deg, var(--graphic-green) 0%, var(--graphic-teal) 35%, var(--graphic-blue) 100%);
    opacity: 0.9;
  }
  .brand {
    position: absolute;
    left: 36px;
    top: 36px;
    display: flex;
    align-items: center;
    gap: 16px;
  }
  .brand-dot {
    width: 92px;
    height: 92px;
    border-radius: 50%;
    background: var(--brand-blue);
    flex: none;
  }
  .brand-name {
    max-width: 330px;
    font-size: 30px;
    line-height: 36px;
    font-weight: 500;
    color: var(--brand-blue);
    letter-spacing: 1px;
  }
  .person-name {
    position: absolute;
    left: 172px;
    top: 165px;
    margin: 0;
    font-size: 34px;
    font-weight: 500;
    color: var(--name-blue);
  }
  .person-title {
    position: absolute;
    left: 172px;
    top: 210px;
    margin: 0;
    font-size: 27px;
    font-weight: 400;
    color: var(--title-green);
  }
  .address {
    position: absolute;
    left: 172px;
    top: 258px;
    margin: 0;
    font-style: normal;
    font-size: 25px;
    line-height: 36px;
    color: var(--body-text);
  }
  .contact-list {
    position: absolute;
    left: 172px;
    top: 345px;
    margin: 0;
    padding: 0;
    list-style: none;
    font-size: 24px;
    color: var(--body-text);
  }
  .contact-list li {
    display: flex;
    align-items: center;
    height: 38.5px;
    padding-left: 14px;
  }
  .contact-list svg {
    width: 24px;
    height: 24px;
    margin-right: 12px;
    fill: var(--icon-blue);
    flex: none;
  }
</style>
</head>
<body>
  <div class="business-card">
    <div class="brand-graphic" role="img" aria-label="Large brand graphic in green and blue tones"></div>

    <div class="brand">
      <div class="brand-dot"></div>
      <span class="brand-name">HARLOW RIDGE CONSTRUCTION</span>
    </div>

    <h1 class="person-name">Mark Ellison</h1>
    <p class="person-title">President</p>

    <address class="address">2710 Harbor Lane<br>Glenwood, NY 11020</address>

    <ul class="contact-list">
      <li>
        <svg viewBox="0 0 24 24" aria-hidden="true"><path d="M2 8c0-3 4-5 10-5s10 2 10 5v2h-5V8H7v2H2z"/><path d="M5 11h14l2 9H3z"/><circle cx="12" cy="15.5" r="2.5" fill="#f6f8fa"/></svg>
        555 0142 7781
      </li>
      <li>
        <svg viewBox="0 0 24 24" aria-hidden="true"><rect x="6" y="1" width="12" height="22" rx="2"/><rect x="8" y="4" width="8" height="13" fill="#f6f8fa"/><circle cx="12" cy="20" r="1.2" fill="#f6f8fa"/></svg>
        555 0198 3406
      </li>
      <li>
        <svg viewBox="0 0 24 24" aria-hidden="true"><rect x="6" y="2" width="12" height="7"/><rect x="2" y="9" width="20" height="10" rx="1"/><rect x="6" y="15" width="12" height="7" fill="#f6f8fa" stroke="#1f3f6e" stroke-width="2"/></svg>
        555 0167 2290
      </li>
      <li>
        <svg viewBox="0 0 24 24" aria-hidden="true"><path d="M2 5h20v14H2z"/><path d="M3 6l9 7 9-7" fill="none" stroke="#f6f8fa" stroke-width="2"/></svg>
        mark@example.com
      </li>
      <li>
        <svg viewBox="0 0 24 24" aria-hidden="true"><circle cx="12" cy="12" r="10"/><path d="M7 7c3 1 3 4 1 6s1 5 3 6M15 5c-1 3 2 4 4 5" fill="none" stroke="#f6f8fa" stroke-width="1.6"/></svg>
        www.example.com
      </li>
    </ul>
  </div>
</body>
</html>
```